Zolvana Stationary and Branding Documents

Corporate Identity Branding stationary needed for IT Recruiting Firm.

I already have a Logo, business cards and website. I need to get designs completed for the remaining corporate identity documents.

The documentation should use similar colors as my website and business card. The designs should modern and clean.

http://zolvanaworks.example/

Target Market(s)

Information Technology Industry

Industry/Entity Type

Information Technology

Colors
3377b5
0255a3
fbee3e
f78f20
f37122
33a6d7
000000
0592cd

Requirements
Must have
• Letter Head
• Folder Design
• PowerPoint Design
• Invoice
• Envelope
Nice to have
• Proposal
• Flyer
• Brochure
Should not have
• Logo
• Business Cards
• Website

```html
<!DOCTYPE html>
<html lang="en">
<head>
<meta charset="utf-8">
<title>Zolvana Stationery Set</title>
<link href="https://fonts.googleapis.com/css2?family=Questrial&family=Cinzel:wght@400&display=swap" rel="stylesheet">
<style>
:root{
  --blue:#0255a3;
  --blue-mid:#3377b5;
  --blue-light:#1a7bc9;
  --orange:#f37122;
  --orange-soft:#f78f20;
  --charcoal:#333333;
  --paper:#ffffff;
  --row:#ececec;
  --ink:#555555;
  --bg:#ffffff;
}
*{box-sizing:border-box;margin:0;padding:0}
html,body{width:1200px;height:1200px;overflow:hidden;background:var(--bg)}
body{position:relative;font-family:"Questrial",sans-serif;color:var(--ink)}
.sheet{position:absolute;background:var(--paper);box-shadow:0 2px 6px rgba(0,0,0,.25);overflow:hidden}
.edge-mark{position:absolute;width:4px}
.edge-mark.orange{background:var(--orange)}
.edge-mark.blue{background:var(--blue)}
.brand-name{font-family:"Questrial",sans-serif;color:var(--blue);letter-spacing:.5px;line-height:1;display:flex;align-items:center;gap:6px}
.brand-name .dot{width:.28em;height:.28em;background:var(--orange);display:inline-block}
.swoosh{position:absolute;left:0;bottom:0;width:100%}
.contact{position:absolute;list-style:none;color:var(--ink);line-height:1.45}
.contact li{display:flex;align-items:center;gap:3px}
.contact .ico{width:.8em;height:.8em;border-radius:50%;background:var(--blue-mid);display:inline-block}

/* letterhead */
.letterhead{left:73px;top:30px;width:385px;height:544px}
.letterhead .brand-name{position:absolute;left:14px;top:26px;font-size:25px}
.letterhead .contact{right:14px;top:22px;font-size:4.5px}

/* invoice */
.invoice{left:516px;top:33px;width:419px;height:542px;font-size:5.5px}
.invoice .brand-name{position:absolute;left:38px;top:32px;font-size:26px}
.invoice .head-rule{position:absolute;left:160px;right:40px;top:61px;border-top:1px solid var(--blue)}
.invoice .head-address{position:absolute;right:40px;top:52px;color:var(--orange);font-size:4.5px;font-weight:bold}
.invoice .head-contact{position:absolute;right:40px;top:63px;font-size:4.5px;color:var(--blue)}
.invoice-title{position:absolute;left:39px;top:88px;color:var(--orange);font-size:18px;font-weight:normal}
.invoice-dates{position:absolute;left:39px;top:111px;font-size:6px;line-height:1.5;color:#888}
.parties{position:absolute;left:39px;top:133px;width:341px;height:76px;border:1px solid var(--orange);display:flex;gap:2px;padding:1px}
.party{flex:1;display:flex;flex-direction:column}
.party-head{background:var(--blue);color:#fff;font-size:8px;padding:5px 6px;height:20px}
.party-body{flex:1;display:flex;gap:4px;padding:3px}
.party-logo{width:40px;display:flex;align-items:center;justify-content:center;border:1px solid #eee;color:#bbb;font-size:7px}
.party-logo .brand-name{position:static;font-size:8px}
.party-fields{flex:1;display:flex;flex-direction:column;gap:1.5px}
.party-fields span{background:var(--row);padding:1px 2px;font-size:4.5px}
.items-label{position:absolute;left:42px;top:217px;font-size:7px;color:#444}
.items{position:absolute;left:39px;top:231px;width:341px;border-collapse:separate;border-spacing:0 3px;font-size:5px}
.items th{background:var(--orange);color:#fff;font-weight:normal;text-align:left;padding:6px 9px;height:20px}
.items td{background:var(--row);padding:6px 9px;height:20px;border-right:2px solid #fff}
.items .num{text-align:center}
.items .money{text-align:center}
.notes{position:absolute;left:39px;top:411px;width:219px;height:68px;border:1px solid #ddd;padding:8px 6px;font-size:5.5px}
.notes .line{border-bottom:1px solid #eee;height:10px}
.notes-foot{position:absolute;left:41px;top:486px;font-size:3.8px}
.amount{position:absolute;left:274px;top:406px;width:105px;font-size:5px}
.amount-head{background:var(--blue);color:#fff;text-align:center;font-size:8px;padding:5px 0}
.amount-row{display:flex;border-bottom:1px solid #fff;background:#f1f1f1}
.amount-row span{flex:1;padding:5px 4px;text-align:right}
.amount-row.total{background:#fff;align-items:center}
.amount-row.total strong{font-weight:normal;font-size:11px;color:var(--blue)}

/* folder */
.folder{left:73px;top:595px;width:436px;height:580px;background:linear-gradient(180deg,var(--blue-light) 0%,var(--blue) 55%,#0a4a8a 100%)}
.folder .brand-name{position:absolute;left:0;right:0;top:82px;justify-content:center;color:#fff;font-size:64px;letter-spacing:1px}
.folder-art{position:absolute;left:0;top:230px;width:436px;height:312px}
.folder-footer{position:absolute;left:0;bottom:0;width:100%;height:40px;background:linear-gradient(180deg,#fafafa,#cfd3d8);display:flex;align-items:center;justify-content:center;font-family:"Cinzel",serif;font-size:15px;color:#2b2b2b;letter-spacing:1px}

/* envelope */
.envelope-front{left:553px;top:598px;width:584px;height:293px}
.envelope-front .brand-name{position:absolute;left:25px;top:30px;font-size:38px}
.envelope-front .contact{left:473px;top:29px;font-size:7px}
.envelope-back{left:551px;top:910px;width:587px;height:275px;background:var(--blue)}
</style>
</head>
<body>

<!-- Letterhead -->
<section class="sheet letterhead" aria-label="Letterhead">
  <span class="edge-mark orange" style="left:0;top:20px;height:21px"></span>
  <span class="edge-mark blue" style="left:0;top:42px;height:22px"></span>
  <span class="edge-mark orange" style="right:0;top:20px;height:21px"></span>
  <span class="edge-mark blue" style="right:0;top:42px;height:22px"></span>
  <div class="brand-name">Zolvana</div>
  <ul class="contact">
    <li><i class="ico"></i>48 Harbor Point 210</li>
    <li style="padding-left:6px">Linden Avenue SE</li>
    <li><i class="ico"></i>5550102938</li>
    <li><i class="ico"></i>info@zolvanaworks.example</li>
    <li><i class="ico"></i>www.zolvanaworks.example</li>
  </ul>
  <svg class="swoosh" viewBox="0 0 385 60" height="60" preserveAspectRatio="none">
    <polygon points="0,13 230,29 0,60" fill="var(--charcoal)"/>
    <polygon points="180,24 300,28 230,29" fill="var(--orange)"/>
    <path d="M30,60 C150,40 270,20 385,0 L385,60 Z" fill="var(--blue)"/>
  </svg>
</section>

<!-- Invoice -->
<section class="sheet invoice" aria-label="Invoice">
  <span class="edge-mark orange" style="left:0;top:34px;height:21px"></span>
  <span class="edge-mark blue" style="left:0;top:56px;height:22px"></span>
  <span class="edge-mark orange" style="right:0;top:34px;height:21px"></span>
  <span class="edge-mark blue" style="right:0;top:56px;height:22px"></span>
  <div class="brand-name">Zolvana</div>
  <div class="head-address">48 Harbor Point 210, Linden Avenue SE</div>
  <div class="head-rule"></div>
  <div class="head-contact">5550102938 · info@zolvanaworks.example</div>

  <h1 class="invoice-title">Invoice 0001</h1>
  <p class="invoice-dates">01 September , 2012<br>Payment due by 25 November 2012</p>

  <div class="parties">
    <div class="party">
      <div class="party-head">FROM</div>
      <div class="party-body">
        <div class="party-logo"><span class="brand-name">Zolvana</span></div>
        <div class="party-fields"><span>Your Address</span><span>Address line 1</span><span>Town</span><span>Region/State</span><span>Zip/Postal Code</span></div>
      </div>
    </div>
    <div class="party">
      <div class="party-head">TO</div>
      <div class="party-body">
        <div class="party-logo">LOGO</div>
        <div class="party-fields"><span>Your Address</span><span>Address line 1</span><span>Town</span><span>Region/State</span><span>Zip/Postal Code</span></div>
      </div>
    </div>
  </div>

  <div class="items-label">ITEMS</div>
  <table class="items">
    <thead><tr><th style="width:48px">Quantity</th><th>Description</th><th style="width:54px">Unit Price</th><th style="width:56px">TOTAL</th></tr></thead>
    <tbody>
      <tr><td class="num">2</td><td>Donec ac erat vel neque molestie convallis.</td><td class="money">$600</td><td class="money">$1200</td></tr>
      <tr><td class="num">1</td><td>Sed eget risus ac lacus tempus sollicitudin in at magna.</td><td class="money">$300</td><td class="money">$300</td></tr>
      <tr><td class="num">3</td><td>Nunc auctor nisl vel lorem aliquet pellentesque.</td><td class="money">$800</td><td class="money">$2400</td></tr>
      <tr><td class="num">2</td><td>Pellentesque habitant morbi.</td><td class="money">$20</td><td class="money">$40</td></tr>
      <tr><td class="num">2</td><td>In hac habitasse platea dictumst, mauris at.</td><td class="money">$2500</td><td class="money">$5000</td></tr>
      <tr><td class="num">1</td><td>Aenean eget enim eget augue dictum fringilla et vitae.</td><td class="money">$100</td><td class="money">$100</td></tr>
    </tbody>
  </table>

  <div class="notes">Special Notes<div class="line"></div><div class="line"></div><div class="line"></div></div>
  <p class="notes-foot">molestie condimentum, Curabitur mi dui, faucibus sed</p>

  <div class="amount">
    <div class="amount-head">AMOUNT DUE</div>
    <div class="amount-row"><span>SUBTOTAL</span><span>$9,040</span></div>
    <div class="amount-row"><span>TAX</span><span>$00.00</span></div>
    <div class="amount-row"><span>SHIPPING</span><span>$00.00</span></div>
    <div class="amount-row total"><span>TOTAL <strong>$9,040.00</strong></span></div>
  </div>

  <svg class="swoosh" viewBox="0 0 419 60" height="60" preserveAspectRatio="none">
    <polygon points="0,13 250,28 0,60" fill="var(--charcoal)"/>
    <polygon points="200,24 330,27 250,28" fill="var(--orange)"/>
    <path d="M90,60 C200,45 310,20 419,0 L419,60 Z" fill="var(--blue)"/>
  </svg>
</section>

<!-- Presentation folder -->
<section class="sheet folder" aria-label="Presentation folder cover">
  <div class="brand-name">Zolvana<span class="dot" style="background:var(--orange-soft)"></span></div>
  <svg class="folder-art" viewBox="0 0 436 312" preserveAspectRatio="none">
    <path d="M0,312 L0,280 C60,140 150,170 260,150 C360,130 410,90 436,0 L436,312 Z" fill="#e6e9ee"/>
  </svg>
  <svg class="folder-art" viewBox="0 0 436 312" preserveAspectRatio="none" role="img" aria-label="Photo of a smiling business team reviewing work together in a bright office">
    <defs>
      <linearGradient id="photoTone" x1="0" y1="0" x2="1" y2="1">
        <stop offset="0" stop-color="#bcd8ea"/>
        <stop offset=".5" stop-color="#8fb7d2"/>
        <stop offset="1" stop-color="#3f6a8f"/>
      </linearGradient>
    </defs>
    <path d="M0,312 L0,296 C60,160 150,190 262,166 C362,146 414,106 436,24 L436,312 Z" fill="url(#photoTone)"/>
  </svg>
  <div class="folder-footer">JOIN THE ELITE</div>
</section>

<!-- Envelope front -->
<section class="sheet envelope-front" aria-label="Envelope front">
  <span class="edge-mark orange" style="left:0;top:20px;height:31px"></span>
  <span class="edge-mark blue" style="left:0;top:52px;height:30px"></span>
  <span class="edge-mark orange" style="right:0;top:20px;height:31px"></span>
  <span class="edge-mark blue" style="right:0;top:52px;height:30px"></span>
  <div class="brand-name">Zolvana</div>
  <ul class="contact">
    <li><i class="ico"></i>48 Harbor Point 210</li>
    <li style="padding-left:9px">Linden Avenue SE</li>
    <li><i class="ico"></i>5550102938</li>
    <li><i class="ico"></i>info@zolvanaworks.example</li>
    <li><i class="ico"></i>www.zolvanaworks.example</li>
  </ul>
  <svg class="swoosh" viewBox="0 0 584 73" height="73" preserveAspectRatio="none">
    <polygon points="0,17 300,37 0,73" fill="var(--charcoal)"/>
    <polygon points="230,32 410,35 300,37" fill="var(--orange)"/>
    <path d="M90,73 C260,55 420,28 584,0 L584,73 Z" fill="var(--blue)"/>
  </svg>
</section>

<!-- Envelope back -->
<section class="sheet envelope-back" aria-label="Envelope back">
  <svg width="587" height="275" viewBox="0 0 587 275">
    <path d="M8,10 L280,145 Q293,152 306,145 L579,10" fill="none" stroke="#034a8e" stroke-width="2"/>
    <path d="M8,265 L250,150 M579,265 L337,150" fill="none" stroke="#034a8e" stroke-width="1.5" opacity=".6"/>
  </svg>
</section>

</body>
</html>
```